Real estate broker business card

Want a modern celan but effective business card for my residential and commercial real estate business. I want the back of the card to advertise my services and to capture business. I have attached the back of my current business card fore ideas
Updates

Logos, photo and text updates added! Added Saturday, September 3, 2016

Project Deadline Extended Reason: LOGOS, PHOTOS AND TEST JUST UPLOADED! I'M READY TO PICK A DESIGN! THANK YOU! Added Saturday, September 3, 2016

Target Market(s)

home buyers and seller. commercial buyers and sellers

Industry/Entity Type

Real Estate

Contact Information for Business Card

must have my contact information and my photo

Requirements
Must have
• Carla Ventrino
• Owner & Qualifying Broker
• Ventrino Real Estate Services
• 505.718.2094
• carla@ventrinohomes.example
• www.ventrinohomes.example
Nice to have
• metallic
• Business capture text: " Don't buy or lease property without someone looking out for your best interests. I will represent you on your home or investment purchase for FREE!"
• "Home owners, call today to receive a FREE market analysis for your homes value!

```html
<!DOCTYPE html>
<html lang="en">
<head>
<meta charset="utf-8">
<title>Ventrino Real Estate Services – Business Card</title>
<link rel="stylesheet" href="https://fonts.googleapis.com/css2?family=Cinzel:wght@400;600&family=Josefin+Sans:wght@300;400&display=swap">
<style>
  :root {
    --page-bg: #e8e6e3;
    --silver-light: #dfe2e4;
    --silver-mid: #b9bec2;
    --silver-dark: #8f959a;
    --band-dark: #0f1113;
    --band-mid: #23272a;
    --teal: #1f6b74;
    --teal-bright: #2f8c96;
    --text-light: #c9cccd;
    --photo-dark: #2a2422;
    --photo-light: #cdbfb8;
  }
  * { margin: 0; padding: 0; box-sizing: border-box; }
  html, body {
    width: 1200px; height: 969px; overflow: hidden;
    background: var(--page-bg);
  }
  .business-card {
    position: absolute; left: 100px; top: 198px;
    width: 1000px; height: 572px;
    border-radius: 6px; overflow: hidden;
    box-shadow: 0 14px 40px rgba(0,0,0,.25);
    background: var(--band-dark);
  }
  .card-top {
    position: absolute; left: 0; top: 0; width: 100%; height: 336px;
    background: linear-gradient(100deg, var(--silver-dark) 0%, var(--silver-light) 45%, var(--silver-mid) 75%, var(--silver-light) 100%);
  }
  .agent-photo {
    position: absolute; left: 48px; top: 22px; width: 276px; height: 314px;
    border-radius: 120px 120px 0 0;
    background: linear-gradient(180deg, var(--photo-dark) 0%, #5a4a44 45%, var(--photo-light) 100%);
  }
  .brand {
    position: absolute; left: 436px; top: 118px;
    display: flex; align-items: center; gap: 26px;
    color: var(--teal);
    font-family: "Cinzel", serif; font-weight: 600;
  }
  .brand-mark {
    width: 96px; height: 96px; background: var(--teal);
  }
  .brand-name { font-size: 58px; line-height: 1; letter-spacing: 2px; }
  .brand-sub { font-size: 20px; letter-spacing: 4px; margin-top: 8px; }
  .card-band {
    position: absolute; left: 0; top: 336px; width: 100%; height: 236px;
    border-top: 4px solid var(--teal);
    background: linear-gradient(180deg, var(--band-mid) 0%, var(--band-dark) 60%);
  }
  .agent-name {
    position: absolute; left: 48px; top: 30px;
    font-family: "Cinzel", serif; font-weight: 400;
    font-size: 36px; color: var(--teal-bright); letter-spacing: 1px;
  }
  .agent-role {
    position: absolute; left: 48px; top: 92px;
    font-family: "Josefin Sans", sans-serif; font-weight: 300;
    font-size: 22px; line-height: 33px; color: var(--text-light);
    text-transform: uppercase; letter-spacing: .5px;
  }
  .contact-list {
    position: absolute; left: 540px; right: 40px; top: 38px; list-style: none;
    font-family: "Josefin Sans", sans-serif; font-weight: 300;
    font-size: 21px; color: var(--text-light); text-transform: uppercase;
    white-space: nowrap;
  }
  .contact-list li { display: flex; align-items: center; gap: 12px; height: 37px; }
  .contact-list svg { width: 19px; height: 19px; fill: var(--teal-bright); flex: none; }
  .offer-line {
    position: absolute; left: 40px; right: 40px; top: 190px; text-align: center;
    font-family: "Josefin Sans", sans-serif; font-weight: 400;
    font-size: 18px; color: var(--teal); text-transform: uppercase; letter-spacing: .5px;
    white-space: nowrap;
  }
</style>
</head>
<body>
  <main class="business-card">
    <section class="card-top">
      <div class="agent-photo" role="img" aria-label="Portrait photo of Carla Ventrino"></div>
      <div class="brand">
        <div class="brand-mark"></div>
        <div>
          <div class="brand-name">VENTRINO</div>
          <div class="brand-sub">REAL ESTATE SERVICES</div>
        </div>
      </div>
    </section>
    <section class="card-band">
      <h1 class="agent-name">Carla Ventrino</h1>
      <p class="agent-role">Owner &amp; Qualifying Broker<br>Ventrino Real Estate Services</p>
      <ul class="contact-list">
        <li>
          <svg viewBox="0 0 24 24" aria-hidden="true"><path d="M6.6 10.8a15.1 15.1 0 0 0 6.6 6.6l2.2-2.2a1 1 0 0 1 1-.25 11.4 11.4 0 0 0 3.6.57 1 1 0 0 1 1 1V20a1 1 0 0 1-1 1A17 17 0 0 1 3 4a1 1 0 0 1 1-1h3.5a1 1 0 0 1 1 1c0 1.25.2 2.45.57 3.57a1 1 0 0 1-.25 1z"/></svg>
          505.718.2094
        </li>
        <li>
          <svg viewBox="0 0 24 24" aria-hidden="true"><path d="M2 5h20v14H2zM3.5 6.5 12 13l8.5-6.5z" fill-rule="evenodd"/></svg>
          carla@ventrinohomes.example
        </li>
        <li>
          <svg viewBox="0 0 24 24" aria-hidden="true"><path d="M12 2a10 10 0 1 0 0 20 10 10 0 0 0 0-20zm0 2c.9 0 2.2 1.8 2.7 5H9.3C9.8 5.8 11.1 4 12 4zM4.3 11h3a17 17 0 0 0 0 2h-3a8 8 0 0 1 0-2zm5 0h5.4a15 15 0 0 1 0 2H9.3a15 15 0 0 1 0-2zm7.4 0h3a8 8 0 0 1 0 2h-3a17 17 0 0 0 0-2zM9.3 15h5.4c-.5 3.2-1.8 5-2.7 5s-2.2-1.8-2.7-5z"/></svg>
          www.ventrinohomes.example
        </li>
      </ul>
      <p class="offer-line">Home owners, call today to receive a free market analysis for your homes value!</p>
    </section>
  </main>
</body>
</html>
```